Lawn Bowls Travel Package Flyer and Poster

We are a New Zealand Travel Company and need a flyer to promote our Lawn Bowls Tours to 3 Destination for our customers... 1) Brochure Size is A4 and with a tri fold design 2) Also a poster A4 Size to be placed in the bowls club to promote our tours and destinations with contact details Outside Page Info Page 1 – Picture(s) overview Page 2 Intro Our winters bowls tours offer a chance to join a like-minded group of friends and bowling enthusiasts for the unique lawn bowls experience. All three tours are fully hosted and include return flights, quality accommodation, numerous groups meals, sightseeing activities, bowls fees plus much more these are a fantastic bowling tours that will truly bowl you over!. Non bowlers are very welcome on all tours as the bowls component is only part the total tour experience. Tour Manager and Bowls Ambassador Peter Marsh is an avid bowler and member of the Kerrigan Vale Bowling Club. Peter has been a European Tour Manager, Cruise Director and is an all-round good guy. Most recently as Tidewell Party Journeys Bowls Ambassador he has help design our last 8 Winter Tours and leads our bowling tours. His experience, assistance, wit and knowledge will ensure that you all have a great deal of fun on tour. Sightseeing & Meals All tours include pre-booked admissions to extensive and diverse range of the most popular sightseeing attractions in all destinations. Along with a number of group meals so the group can enjoy some culinary delights and opportunities to socialise. You're never alone and non-bowlers welcome We know that this Bowling holiday is a great way to meet new people and make new friends so we encourage those travelling solo to join us! Of course, you will have a guaranteed single room when you purchase the single price, however if you prefer not to pay the additional fee, we will match you with another single traveller of the same gender on a shared basis. Occasionally there will be an instance where there are no other single guests and in these cases you will have to pay the single supplement. Whilst we do try our best to match roommates, compatibility cannot be guaranteed and this offer is conditional on acceptance of this factor. Pre or Post Touring We are able to accommodate individuals who are wishing to see more of the destination either before or after the Tour – please contact us to discuss your touring requirements. Page 3 - Contact details Contact us today for a more details itinerary on all or any of the above tours Contact Details Tidewell Party Journeys PO Box 51-946 Halsworth Mail Centre Website - www.tidewellpartyjourneys.com Email – bowls@tidewellpartyjourneys.com Freephone Phone – 0800 382 915 M 027 904 3726 Inside Pages Page 1 Tour 1 – Niue Dates – 19 June – 27 June 2020 About Niue is a Pacific paradise located north east of New Zealand and is just a 3 ½ hour flight from Auckland. One of the smallest countries, and one of the largest raised coral atolls on earth. Niue is a place where it’s normal for complete strangers to wave at each other, all the time. It’s a place where nature hasn’t been broken… and things are ‘The way they used to be’. Come and enjoy our beautiful little island. Make history and join us on at the first bowls week to held in Niue will included 3 days of bowls on Niue during the week along with a number of sightseeing activities on the Island Small Picture of bowls club Price from $ x twin/double share Page 2 Tour 2 - Norfolk Island Dates – 06 August -14 August 2020 Price from $x twin/double share About Norfolk Island is a popular lawn bowls destination, unlike some clubs in Australia and New Zealand the Norfolk greens remain open all year round. With recent reintroduce of direct from New Zealand we are delighted to offer a Tour to Norfolk Island where the locals are very welcoming to New Zealand to their greens. This is the bowls week to held will included 3 days of bowls during the week with a number of sightseeing activities on the island. Also for those wishing to extend onwards we are offering the option to combine with our Sunshine Coast Tour with a flight from Norfolk to Brisbane Small Picture Page 3 Tour 3 - Sunshine Coast Dates – 15 August – 23 August 2020 The Sunshine Coast our most popular tour with stunning winter climate, so join us for all that Queensland has to offer, this is a fantastic bowling tour that will truly bowl you over! An opportunity for you to experience some special events and enjoy the culture, sights, and foods, wines/beers or course some bowls This bowls week will included 3 days of bowls at different bowls clubs during the week with a number of sightseeing activities on the Sunshine Coast. Price from twin/double share Picture or logo Lawn Bowls
Lawn Bowlers in New Zealand for Winter Bowls Tour
Travel
Designer to choose colors to be used in the design.

```html
<!DOCTYPE html>
<html lang="en">
<head>
<meta charset="utf-8">
<title>Winter Bowls Tours – Tidewell Party Journeys</title>
<link rel="stylesheet" href="https://fonts.googleapis.com/css2?family=Didact+Gothic&family=Mulish:wght@800&display=swap">
<style>
  :root {
    --mint: #47fd8a;
    --rust: #cc561f;
    --ink: #15120f;
    --white: #ffffff;
    --black: #0a0a0d;
    --body: "Didact Gothic", "Century Gothic", sans-serif;
    --head: "Mulish", "Century Gothic", sans-serif;
  }
  * { margin: 0; padding: 0; box-sizing: border-box; }
  html, body { width: 1200px; height: 855px; overflow: hidden; background: var(--mint); }
  .sheet {
    position: relative; width: 1200px; height: 855px; overflow: hidden;
    background: var(--mint); color: var(--ink); font-family: var(--body);
  }
  .shapes { position: absolute; inset: 0; }
  .photo-area { position: absolute; left: 795px; top: 0; width: 405px; height: 855px; }

  /* Contact panel */
  .contact { position: absolute; left: 0; top: 0; width: 420px; height: 855px; }
  .contact-title {
    position: absolute; left: 75px; top: 52px;
    font-family: var(--head); font-weight: 800; font-size: 33px; letter-spacing: .3px;
  }
  .contact-intro {
    position: absolute; left: 79px; top: 98px; font-size: 19.5px; line-height: 33.5px;
  }
  .address {
    position: absolute; left: 89px; top: 265px; font-size: 19.5px; line-height: 33.5px;
  }
  .phones {
    position: absolute; left: 141px; top: 420px; font-size: 21.5px; line-height: 25px; letter-spacing: .6px;
  }
  .email {
    position: absolute; left: 0; width: 420px; top: 531px; text-align: center; font-size: 19px;
  }
  .website {
    position: absolute; left: 0; width: 420px; top: 635px; text-align: center; font-size: 19px; letter-spacing: .3px;
  }
  .icon { position: absolute; fill: var(--ink); }
  .partner {
    position: absolute; display: flex; align-items: center; justify-content: center;
    text-align: center; font-family: var(--body); font-size: 17px; line-height: 21px;
  }
  .partner-isle { left: 52px; top: 682px; width: 163px; height: 84px; background: var(--white); color: var(--ink); }
  .partner-company { left: 223px; top: 685px; width: 138px; height: 137px; background: var(--black); color: var(--white); }

  /* Story column */
  .story {
    position: absolute; left: 419px; top: 36px; width: 360px;
    font-size: 15px; line-height: 22.35px;
  }
  .story .ln { display: block; white-space: nowrap; text-align: justify; text-align-last: justify; }
  .story .ln.indent { padding-left: 16px; }
  .story .ln.centre { text-align: center; text-align-last: center; }

  /* Intro in the lower right disc */
  .intro { position: absolute; left: 823px; top: 492px; width: 352px; }
  .intro-title {
    text-align: center; font-family: var(--head); font-weight: 800;
    font-size: 21px; letter-spacing: 5px; margin-bottom: 4px; padding-left: 10px;
  }
  .intro p { font-size: 18px; line-height: 29.3px; }
  .intro .ln { display: block; white-space: nowrap; text-align: justify; text-align-last: justify; }
  .intro .ln.centre { text-align: center; text-align-last: center; }
</style>
</head>
<body>
<main class="sheet">
  <svg class="shapes" width="1200" height="855" viewBox="0 0 1200 855">
    <defs>
      <linearGradient id="clubhouse-tones" x1="0" y1="0" x2="0" y2="1">
        <stop offset="0" stop-color="#a79aa3"/>
        <stop offset=".18" stop-color="#c9a9ad"/>
        <stop offset=".3" stop-color="#2f5a1f"/>
        <stop offset=".52" stop-color="#3b5a20"/>
        <stop offset=".56" stop-color="#8d97b3"/>
        <stop offset=".64" stop-color="#6f7f9f"/>
        <stop offset=".72" stop-color="#7c8a66"/>
        <stop offset="1" stop-color="#5c7a45"/>
      </linearGradient>
    </defs>
    <rect class="photo-area" x="795" y="0" width="405" height="855" fill="url(#clubhouse-tones)"
          role="img" aria-label="Photograph of a lawn bowls clubhouse with its sign, trees behind and the green in front"/>
    <ellipse cx="190" cy="150" rx="320" ry="390" fill="var(--rust)"/>
    <circle cx="1122" cy="905" r="442" fill="var(--rust)"/>
  </svg>

  <section class="contact">
    <h1 class="contact-title">Contact Details</h1>
    <p class="contact-intro">Contact us today for more<br>details itinerary on all or<br>any of the above tours.</p>

    <svg class="icon" style="left:185px;top:216px" width="48" height="46" viewBox="0 0 48 46" aria-hidden="true">
      <path d="M24 2 L2 22 L7 22 L7 44 L41 44 L41 22 L46 22 L36 13 L36 4 L31 4 L31 8.5 Z M11 22 L24 10 L37 22 L37 40 L28 40 L28 28 L20 28 L20 40 L11 40 Z"/>
    </svg>
    <p class="address">Tidewell Party Journeys<br>PO Box 51-946 Halsworth<br>Mail Centre.</p>

    <svg class="icon" style="left:189px;top:366px" width="40" height="40" viewBox="0 0 40 40" aria-hidden="true">
      <path d="M9 2 C6 2 2 6 2 11 C3 25 15 37 29 38 C34 38 38 34 38 31 L38 28 L29 23 L24 28 C19 26 14 21 12 16 L17 11 L12 2 Z"/>
    </svg>
    <p class="phones">0800 382 915<br>027 904 3726</p>

    <svg class="icon" style="left:186px;top:484px" width="47" height="35" viewBox="0 0 47 35" aria-hidden="true">
      <path d="M0 0 H47 V35 H0 Z M4 4 V31 H43 V4 Z" />
      <path d="M4 4 L23.5 20 L43 4 M4 31 L18 17 M43 31 L29 17" fill="none" stroke="var(--ink)" stroke-width="3"/>
    </svg>
    <p class="email">bowls@tidewellpartyjourneys.com</p>

    <svg class="icon" style="left:186px;top:574px" width="50" height="52" viewBox="0 0 50 52" aria-hidden="true">
      <g fill="none" stroke="var(--ink)" stroke-width="4">
        <circle cx="23" cy="23" r="20"/>
        <ellipse cx="23" cy="23" rx="8" ry="20"/>
        <path d="M3 23 H43 M7 12 H39 M7 34 H24"/>
      </g>
      <path d="M26 26 L48 36 L39 38 L45 48 L41 50 L35 40 L29 46 Z"/>
    </svg>
    <p class="website">www.tidewellpartyjourneys.com</p>

    <div class="partner partner-isle">Coralis Isle Tourism</div>
    <div class="partner partner-company">Tidewell Party<br>Journeys</div>
  </section>

  <section class="story">
    <span class="ln indent">Non bowlers are very welcome on all tours as</span>
    <span class="ln">the bowls component is only a part of the total</span>
    <span class="ln">experience. Tour Manager and Bowls Ambassador</span>
    <span class="ln">Peter Marsh is an avid bowler and member of</span>
    <span class="ln">the Kerrigan Vale Bowling Club. Peter has been</span>
    <span class="ln">a European Tour Manager, Cruise Director and is</span>
    <span class="ln">an all-round good guy. Most recently as Tidewell</span>
    <span class="ln">Party Journeys Bowls Ambassador he has</span>
    <span class="ln">help design our last 8 Winter Tours and lead our</span>
    <span class="ln">bowling tours. His experience, assistance, wit and</span>
    <span class="ln">knowledge will ensure that you all have a great</span>
    <span class="ln">deal of fun on tour. All tours include pre-booked</span>
    <span class="ln">admissions to extensive and diverse range of the</span>
    <span class="ln">most popular sightseeing attractions in all</span>
    <span class="ln">destinations. Along with a number of group meals</span>
    <span class="ln">so the group can enjoy some culinary delights and</span>
    <span class="ln">opportunities to socialise. You're never alone. We</span>
    <span class="ln">know that this Bowling holiday is a great way to</span>
    <span class="ln">meet new people and make new friends so we</span>
    <span class="ln">encourage those travelling solo to join us! Of</span>
    <span class="ln">course, you will have a guaranteed single room</span>
    <span class="ln">when you purchase the single price, however if you</span>
    <span class="ln">prefer not to pay the additional fee, we will match</span>
    <span class="ln">you with another single traveller of the same</span>
    <span class="ln">gender on a shared basis. Occasionally there will</span>
    <span class="ln">be an instance where there are no other single</span>
    <span class="ln">guests and in these cases you will have to pay the</span>
    <span class="ln">single supplement. Whilst we do try our best to</span>
    <span class="ln">match roommates, compatibility cannot be</span>
    <span class="ln">guaranteed and this offer is conditional on</span>
    <span class="ln">acceptance of this factor. Pre or Post Touring We</span>
    <span class="ln">are able to accommodate individuals who are</span>
    <span class="ln">wishing to see more of the destination either</span>
    <span class="ln centre">before or after the tour.</span>
    <span class="ln centre">Please contact us to discuss your requirements.</span>
  </section>

  <section class="intro">
    <h2 class="intro-title">Our</h2>
    <p>
      <span class="ln centre">winters bowls tours offer a chance</span>
      <span class="ln">to join a like-minded groups of friends and</span>
      <span class="ln">bowling enthusiasts for a unique lawn</span>
      <span class="ln">bowls experience. All three tours are fully</span>
      <span class="ln">hosted, it includes return flights, quality</span>
      <span class="ln">accommodation, numerous group meals,</span>
      <span class="ln">sightseeing activities, bowls fees and much</span>
      <span class="ln">more. These are a fantastic bowling tours</span>
      <span class="ln centre">that will truly bowl you over!</span>
    </p>
  </section>
</main>
</body>
</html>
```